Meadow Paw Web Site

We have basically a start up business that I need help with. This project is just for the web site.

Our product is a frozen raw pet food that promotes weight control, less shedding, smaller stools and an overall better health. The product is in nugget form similar to what you would see in a steak shish kabob. I only share that with you in case you want to incorporate that in the design.

We have been in business for 17 years but all of our sales have been word of mouth. We are going to be launching an infomercial this summer and I need everything stated previously to be completed before we can launch the infomercial.

We need the following (6) pages:

Home:
This is where we need to have the ability to purchase our products. Our main goal is to get the consumer to purchase our product. We have our own shopping cart so we just need to allow for the insertion of that shopping cart.

Why Raw:
This will just be a page with 4-5 paragraphs and an embedded YouTube video.

How to Use:
We will need a page with a chart (4 Columns wide with 6 rows) as well as an embedded YouTube video.

Customer Success Stories:
Allow us to add these as we move forward. I need a placeholder for an image of the customers pet and a paragraph or two explaining the situation

Where to Buy:
- Online - Find a Retailer - Find a Local Distributor - Call to Order

Contact Us:
Copper Ridge Holdings, Inc.
2740 Copper Rd
Eagan, MN 55148
(800) xxx-xxxx

We need to provide links to our to be created... Facebook page, Twitter Account, Youtube Channel, Google circle, Blog
Updates

All, I have received many front page designs that look good.  Please notice in the brief that I need multiple pages built not just the home page.  

Thanks,

Dale

Reason: I need to see the rest of the pages. Thanks, Dale

Target Market(s)

Women between the ages of 30 & 60.

Industry/Entity Type

Shopping

```html
<!DOCTYPE html>
<html lang="en">
<head>
<meta charset="utf-8">
<title>Meadow Paw – Contact Us</title>
<link rel="stylesheet" href="https://fonts.googleapis.com/css2?family=Oswald:wght@400;500&family=Open+Sans:wght@400;600&display=swap">
<style>
:root{
  --orange:#e06a0c;
  --orange-dark:#c24d05;
  --orange-light:#f08a24;
  --rust:#c6400a;
  --yellow:#f6d21c;
  --ink:#2d2d2d;
  --muted:#6b6b6b;
  --line:#f0d4cc;
  --page:#fbf6f5;
  --footer:#2b2b2d;
  --footer-bottom:#202022;
  --footer-text:#a8a8a8;
}
*{box-sizing:border-box;margin:0;padding:0}
html,body{width:973px;height:1200px;overflow:hidden}
body{position:relative;background:var(--page);font-family:"Open Sans",sans-serif;color:var(--ink)}
.abs{position:absolute}
.hero-bg{left:0;top:0;width:973px;height:495px;background:linear-gradient(90deg,#c9c9c9 0%,#ececec 22%,#ededed 75%,#cfcfcf 100%)}
.top-links{right:97px;top:20px;font:600 9.5px "Open Sans",sans-serif;color:var(--rust);letter-spacing:.2px}
.top-links span{margin:0 4px}
.brand{left:97px;top:28px;width:162px;height:95px;display:flex;align-items:center;gap:8px;justify-content:center}
.brand-mark{width:18px;height:18px;background:var(--orange)}
.brand-name{font:500 24px "Oswald",sans-serif;color:var(--orange-dark)}
.btn-pill{top:53px;height:19px;width:67px;border-radius:10px;font:400 10px "Open Sans",sans-serif;text-align:center;line-height:19px}
.btn-signin{left:734px;background:var(--orange);color:#fff}
.btn-register{left:808px;background:var(--yellow);color:#4a3000}
.cart{left:505px;top:96px;display:flex;align-items:center;gap:8px;font:400 12px "Oswald",sans-serif;color:var(--rust)}
.cart .items{margin-left:22px}
.search{left:701px;top:95px;width:175px;height:26px;border:1px solid #e0c8c0;border-radius:13px;background:#fff;padding:0 14px;display:flex;align-items:center;justify-content:space-between;font:400 10px "Open Sans",sans-serif;color:var(--rust)}
.nav{left:97px;top:139px;width:779px;height:37px;background:linear-gradient(#f07a1a,#d25a06);border-radius:4px;display:flex;color:#fff;font:400 15px "Oswald",sans-serif}
.nav a{display:flex;align-items:center;justify-content:center;color:#fff;text-decoration:none;border-left:1px solid #b84d06}
.nav a:first-child{border-left:none}
.slider{left:97px;top:195px;width:547px;height:266px;background:#dfa487;border-radius:10px;padding:12px}
.slide{width:100%;height:100%;background:linear-gradient(170deg,#4f7d2a 0%,#8ca84a 40%,#d8b07a 70%,#c8955a 100%);position:relative}
.slide-caption{position:absolute;right:16px;bottom:26px;text-align:right;font:400 26px/34px "Oswald",sans-serif;color:#fff;text-shadow:0 1px 3px rgba(0,0,0,.4)}
.side-photo{left:662px;top:194px;width:214px;height:226px;background:linear-gradient(#8a7060 0%,#b38a62 55%,#5f8c2e 100%);border-radius:9px 9px 0 0}
.cta{left:662px;top:420px;width:214px;height:41px;background:linear-gradient(#f07a1a,#d25a06);border-radius:0 0 9px 9px;color:#fff;font:400 22px/41px "Oswald",sans-serif;text-align:center;letter-spacing:1px}
.dots{left:334px;top:471px;display:flex;gap:7px}
.dots i{width:9px;height:9px;border-radius:50%;background:#fff;display:block}
.dots i.on{background:var(--orange);box-shadow:0 0 0 2px #f5c9a0}
.section-bar{left:97px;top:515px;width:779px;height:36px;background:linear-gradient(#ec7412,#cf5807);border-radius:4px;color:#fff;font:400 16px/36px "Oswald",sans-serif;padding-left:20px}
.card{left:97px;top:577px;width:469px;height:315px;background:#fff;border:1px solid #eadcd8;border-radius:8px;box-shadow:0 3px 0 -1px #fff,0 4px 0 -1px #e6dcda}
.card-title{left:124px;top:596px;font:400 25px "Open Sans",sans-serif;letter-spacing:-1px;color:#333}
.card-rule{left:124px;top:649px;width:426px;height:1px;background:var(--line)}
.field{border:1px solid var(--line);background:#fff;font:400 11px "Open Sans",sans-serif;color:#555;padding:0 16px;display:flex;align-items:center}
.f-name{left:122px;top:682px;width:160px;height:36px}
.f-email{left:122px;top:728px;width:160px;height:36px}
.f-subject{left:122px;top:775px;width:160px;height:36px}
.f-comment{left:290px;top:682px;width:261px;height:128px;align-items:flex-start;padding-top:11px;padding-left:20px}
.submit{left:471px;top:825px;width:80px;height:39px;background:var(--rust);border-radius:5px;color:#fff;font:400 16px/39px "Oswald",sans-serif;text-align:center}
.side-brand{left:616px;top:588px;display:flex;align-items:center;gap:10px;font:600 34px "Open Sans",sans-serif;color:#1e1e1e;letter-spacing:-1px}
.side-brand .mark{width:26px;height:26px;background:#1e1e1e}
.side-rule{left:616px;top:645px;width:260px;height:3px;background:#d9d4d2}
.side-text{left:616px;top:671px;font:400 11px/17px "Open Sans",sans-serif;color:#333;letter-spacing:-.3px}
.side-lines{left:617px;font:400 10.5px/16px "Open Sans",sans-serif;color:#222}
.phones{top:724px}
.emails{top:770px}
.side-social{left:617px;top:820px;display:flex;gap:10px}
.side-social i{width:19px;height:19px;border-radius:50%;background:#555;display:block}
.footer{left:0;top:942px;width:973px;height:223px;background:var(--footer)}
.footer-bottom{left:0;top:1165px;width:973px;height:35px;background:var(--footer-bottom);color:#8a8a8a;font:400 9.5px/35px "Open Sans",sans-serif;padding-left:97px}
.col{top:970px;color:var(--footer-text);font:400 10px/19.5px "Open Sans",sans-serif}
.col h3{font:400 17px "Oswald",sans-serif;color:#fff;margin-bottom:8px;line-height:22px}
.col-sep{top:977px;width:0;height:152px;border-left:1px dotted #555}
.col .small{font-size:8.5px;line-height:16px}
.col .tel{display:flex;align-items:center;gap:6px;margin-top:4px;font-size:11px}
.news-input{left:683px;top:1036px;width:191px;height:26px;background:#fff;border:1px solid #ccc;font:400 11px/26px "Open Sans",sans-serif;color:#bbb;padding-left:10px}
.subscribe{left:805px;top:1070px;width:70px;height:23px;background:var(--rust);color:#fff;font:400 11px/23px "Open Sans",sans-serif;text-align:center}
.foot-social{left:743px;top:1104px;display:flex;gap:7px}
.foot-social i{width:21px;height:21px;border-radius:3px;display:block}
</style>
</head>
<body>
<div class="abs hero-bg"></div>

<div class="abs top-links">MY ACCOUNT<span>/</span>WISH LIST<span>/</span>MY CART<span>/</span>CHECKOUT</div>

<div class="abs brand"><span class="brand-mark"></span><span class="brand-name">Meadow Paw</span></div>

<div class="abs btn-pill btn-signin">Sing in</div>
<div class="abs btn-pill btn-register">Register</div>

<div class="abs cart">
  <svg width="22" height="18" viewBox="0 0 22 18"><path d="M2 6h18l-2.5 10h-13z" fill="none" stroke="#e06a0c" stroke-width="2"/><path d="M7 6l4-5 4 5" fill="none" stroke="#e06a0c" stroke-width="2"/><path d="M8 9v5M11 9v5M14 9v5" stroke="#e06a0c" stroke-width="1.5"/></svg>
  <span>SHOPPING CART</span><span class="items">(2) ITEMS</span>
</div>

<div class="abs search"><span>Search.......</span>
  <svg width="13" height="13" viewBox="0 0 13 13"><circle cx="5.5" cy="5.5" r="4" fill="none" stroke="#c6400a" stroke-width="2"/><path d="M8.5 8.5l3.5 3.5" stroke="#c6400a" stroke-width="2.2"/></svg>
</div>

<nav class="abs nav">
  <a style="width:63px"><svg width="18" height="15" viewBox="0 0 18 15"><path d="M9 0l9 7.5h-2.5V15H11v-4.5H7V15H2.5V7.5H0z" fill="#fff"/></svg></a>
  <a style="width:117px">Why Raw</a>
  <a style="width:139px">How to Use</a>
  <a style="width:155px">Where to Buy</a>
  <a style="width:173px">Success Stories</a>
  <a style="width:132px">Contact Us</a>
</nav>

<div class="abs slider">
  <div class="slide" role="img" aria-label="Three golden puppies resting their paws on a wooden plank in the grass">
    <div class="slide-caption">There are many variations of<br>passages of Lorem</div>
  </div>
</div>
<div class="abs side-photo" role="img" aria-label="Tan puppy running across a grassy lawn"></div>
<div class="abs cta">CALL TO ORDER</div>
<div class="abs dots"><i></i><i></i><i class="on"></i><i></i><i></i></div>

<div class="abs section-bar">Lorem ipsum dolor</div>

<div class="abs card"></div>
<div class="abs card-title">Reach Us</div>
<div class="abs card-rule"></div>
<div class="abs field f-name">Name</div>
<div class="abs field f-email">Email</div>
<div class="abs field f-subject">Subject</div>
<div class="abs field f-comment">Your comment</div>
<div class="abs submit">Submit</div>

<div class="abs side-brand"><span class="mark"></span>Meadow Paw</div>
<div class="abs side-rule"></div>
<div class="abs side-text">Lorem ipsum dolor sit amet, consectetur adipiscing elit.<br>Sed viverra, urna quis dignissim .</div>
<div class="abs side-lines phones">+(00) 000 000 000<br>+(00) 000 000 000</div>
<div class="abs side-lines emails">hello@meadowpaw-mail.com<br>orders@meadowpaw-mail.com</div>
<div class="abs side-social"><i></i><i></i><i></i><i style="background:var(--orange)"></i><i></i></div>

<footer class="abs footer"></footer>
<div class="abs col" style="left:97px"><h3>Quick Links</h3>Why Raw<br>How to Use<br>Where to Buy<br>Success Stories<br>How to Use<br>Where to Buy<br>Contact Us</div>
<div class="abs col-sep" style="left:198px"></div>
<div class="abs col" style="left:221px"><h3>Top Products</h3>Product 1<br>Product 2<br>Product 3<br>Product 4<br>Product 5<br>Product 6<br>Product 7</div>
<div class="abs col-sep" style="left:324px"></div>
<div class="abs col" style="left:347px"><h3>Where to Buy</h3>Find a Retailer<br>Find a Local Distributor<br>Call to Order</div>
<div class="abs col-sep" style="left:472px"></div>
<div class="abs col" style="left:500px;width:160px"><h3>Contact Information</h3>PUBLISHING PACKAGES<div class="small">Lorem Ipsum is therefore always free from repetition</div>
  <div class="tel"><svg width="14" height="14" viewBox="0 0 14 14"><path d="M3 1l2.5 3-1.5 1.5c.8 1.8 2.2 3.2 4 4L9.5 8 13 10.5 11.5 13C6 13 1 8 1 2.5z" fill="#bbb"/></svg>+0 (000) 000-0000</div></div>
<div class="abs col-sep" style="left:661px"></div>
<div class="abs col" style="left:682px;width:200px"><h3>Newsletter</h3><div style="line-height:13px">combined with a handful of model<br>sentence structures.</div></div>
<div class="abs news-input">Email address</div>
<div class="abs subscribe">Subscribe</div>
<div class="abs foot-social"><i style="background:#3b6fc4"></i><i style="background:#3e5873"></i><i style="background:#f4961c"></i><i style="background:#d2382c"></i><i style="background:#c62d25"></i></div>

<div class="abs footer-bottom">Company Name © 2014. Privacy Policy</div>
</body>
</html>
```